Hunting club needs a new web design !

We need a new web design for our hunting club located in Poland, called "BORYNA". The club was founded in 1945. Colors that we would like to see in the project are the colors of the forest. The website should be built in such a way that all text elements can be changed to another language and can't be graphic.
"BORYNA" means - big, thick forest in which the game, small and big resides

Target Market(s)

hunters,

Industry/Entity Type

Hunting

Coding

Coded - Design and coding required

Number of Pages Required

5+ page

Font styles to use
Decorative

Colors

Designer to choose colors to be used in the design.

Requirements
Must have
• current date, calendar,
• must contain almost all materials from our current web page
• http://boryna-lasowiec.webnest.pl/
• new web address: borynalsw.pl
Nice to have
• current weather in three hunting regions that we allowed to hunt, or indicated by the visitor on the map placed on our web,
• actual phase of the moon, actual moon rising hour, actual moon set hour, actual sun rise hour, actual sun set hour, current weather in region (Borków Nadrzeczny, poland)
• wood, forest, deers, boars,
Should not have
• mountain photos, modern look, white or bright backgrounds,

```html
<!DOCTYPE html>
<html lang="pl">
<head>
<meta charset="utf-8">
<title>Koło Łowieckie Boryna w Borkowie Nadrzecznym</title>
<link href="https://fonts.googleapis.com/css2?family=Playfair+Display:wght@400;700&family=Open+Sans:wght@400;600;700&display=swap" rel="stylesheet">
<style>
:root{
  --cream:#efe9dc;
  --forest:#2f6b2a;
  --bark:#3a2416;
  --bark-dark:#24160d;
  --wood:#5a3a24;
  --wood-light:#7a5436;
  --rust:#b8622a;
  --gold:#d9b77a;
  --text-light:#e8dcc8;
  --muted:#b9a78c;
  --panel:#f3efe6;
}
*{box-sizing:border-box;margin:0;padding:0}
html,body{width:1200px;height:2756px;overflow:hidden}
body{font-family:"Open Sans",sans-serif;color:var(--text-light);background:var(--bark)}
h1,h2,h3,.brand-name{font-family:"Playfair Display",serif}

.site-header{height:144px;background:var(--cream);display:flex;align-items:center;padding:0 70px;color:#3a2a1c}
.brand{display:flex;align-items:center;gap:18px}
.brand-name{font-size:54px;font-weight:700;color:var(--forest);letter-spacing:2px}
.brand-mark{width:44px;height:44px;border-radius:50%;background:var(--forest);flex:none}
.brand-club{font-family:"Playfair Display",serif;font-size:19px;line-height:1.2;color:#3a2a1c}
.brand-sub{font-size:10px;color:#6d5d48;margin-top:6px}
.header-tools{margin-left:auto;display:flex;gap:14px;align-items:center}
.sun-times{border:1px solid #c9b99a;background:#fff;padding:8px 12px;font-size:11px;color:var(--rust);font-weight:600}
.lang-select{background:#fff;border:1px solid #c9b99a;padding:8px 10px;font-size:11px;color:#3a2a1c;width:96px}
.moon-box{background:var(--rust);color:#fff;padding:8px 14px;font-size:13px;font-weight:700;line-height:1.2}
.moon-box small{display:block;font-weight:400;font-size:9px}

.main-nav{height:40px;background:var(--bark-dark);display:flex;align-items:center;padding:0 70px;gap:28px}
.main-nav a{color:var(--text-light);text-decoration:none;font-size:13px;font-weight:600}

.hero{height:564px;background:linear-gradient(180deg,#8a8f60 0%,#6d6a3c 45%,#8a6a3a 75%,#5a4324 100%)}

.welcome{height:532px;background:linear-gradient(180deg,#6a4428,#4c2f1c);text-align:center;padding-top:60px}
.welcome h2{font-size:28px;font-weight:400;line-height:1.3;color:#fff}
.welcome h2 span{display:block;font-size:34px}
.divider{width:70px;height:2px;background:var(--gold);margin:16px auto}
.welcome p{width:620px;margin:0 auto 14px;font-size:12px;line-height:1.7;color:var(--text-light)}
.btn{display:inline-block;background:var(--rust);color:#fff;font-size:11px;font-weight:700;padding:8px 18px;text-transform:uppercase;border:0}
.welcome .btn{margin-top:18px}

.widgets{height:400px;background:linear-gradient(180deg,#4c2f1c,#3a2416);display:flex;justify-content:center;gap:36px;padding-top:30px}
.widget{width:330px;height:340px;background:var(--bark-dark);border:1px solid #5a3a24;padding:18px 22px}
.widget h3{text-align:center;font-size:22px;font-weight:400;color:#fff}
.widget .divider{width:40px;margin:8px auto 14px}
.field-label{font-size:11px;color:var(--muted);margin-bottom:4px}
.field{height:26px;background:#5a3a24;border:1px solid #7a5436;margin-bottom:8px;font-size:11px;color:var(--text-light);padding:5px 8px}
.field.tall{height:54px}
.widget .btn{width:100%;text-align:center;margin-top:6px}
.quote{font-size:12px;line-height:1.7;color:var(--text-light);font-style:italic;text-align:center}
.quote-author{text-align:center;font-size:12px;font-weight:700;margin-top:14px;color:var(--gold)}

.content{height:440px;background:linear-gradient(180deg,#3a2416,#5a3a24);padding:16px 70px}
.content-panel{height:410px;background:var(--panel);display:flex;color:#3a2a1c}
.col{padding:16px}
.col h3{font-size:22px;color:var(--forest);font-weight:700;margin-bottom:12px}
.gallery{width:340px}
.g-item{display:flex;gap:12px;margin-bottom:12px}
.g-thumb{width:110px;height:70px;background:linear-gradient(135deg,#6b7a45,#4a3a22)}
.g-item strong{display:block;font-size:13px;margin-top:10px}
.g-item span{font-size:11px;color:#6d5d48}
.monograph{width:380px;background:linear-gradient(180deg,#4a5a2c,#2e3a1c);color:#fff;padding:20px 24px}
.monograph h3{color:#fff;text-transform:uppercase;font-size:18px;letter-spacing:1px}
.monograph ul{list-style:none;font-size:12px;line-height:2}
.monograph li::before{content:"› ";color:var(--gold)}
.news{flex:1}
.n-item{display:flex;gap:10px;margin-bottom:8px}
.n-thumb{width:70px;height:52px;background:linear-gradient(135deg,#a0622a,#4a3a22);flex:none}
.n-item b{display:block;font-size:11px;color:var(--rust)}
.n-item span{font-size:11px;line-height:1.4}
.col .btn{margin-top:4px}

.hunters{height:360px;background:linear-gradient(180deg,#6a5a3a,#4a3a24 60%,#2e2016)}

.site-footer{height:276px;background:var(--bark-dark);padding:30px 70px 0;position:relative}
.footer-cols{display:flex;gap:50px}
.footer-cols h4{font-size:14px;color:#fff;margin-bottom:6px}
.footer-cols .divider{margin:0 0 12px;width:36px}
.footer-cols ul{list-style:none;font-size:11px;line-height:1.9;color:var(--muted)}
.links{display:flex;gap:40px}
.contact{width:200px;font-size:11px;line-height:1.9;color:var(--muted)}
.social li{display:flex;align-items:center;gap:8px}
.social i{width:14px;height:14px;border-radius:50%;background:var(--wood-light);display:inline-block}
.newsletter{width:330px;font-size:11px;line-height:1.6;color:var(--muted)}
.subscribe{display:flex;margin-top:12px}
.subscribe .field{flex:1;margin:0;height:30px}
.subscribe .btn{padding:8px 14px}
.copyright{position:absolute;left:0;right:0;bottom:0;height:40px;border-top:1px solid #3a2416;text-align:center;font-size:11px;line-height:40px;color:var(--muted)}
</style>
</head>
<body>
<header class="site-header">
  <div class="brand">
    <span class="brand-name">BORYNA</span>
    <span class="brand-mark" aria-hidden="true"></span>
    <div>
      <div class="brand-club">Koło Łowieckie Boryna<br>w Borkowie Nadrzecznym</div>
      <div class="brand-sub">Stowarzyszone w Zrzeszeniu Myśliwych Nadrzecznych od 1945 roku</div>
    </div>
  </div>
  <div class="header-tools">
    <div class="sun-times">☀ Sunrise, Sunset, and Moon Times for Today</div>
    <div class="lang-select">Poland ▾</div>
    <div class="moon-box">Moon: 7.9%<small>Waxing Crescent</small></div>
  </div>
</header>

<nav class="main-nav">
  <a href="#">Home</a><a href="#">About Us</a><a href="#">Hunting Area</a><a href="#">Hunting Offer</a><a href="#">Hunting Season</a><a href="#">Weather</a><a href="#">News</a><a href="#">Gallery</a><a href="#">Contact</a>
</nav>

<section class="hero" role="img" aria-label="Jeleń na leśnej polanie obok drewnianej ambony myśliwskiej"></section>

<section class="welcome">
  <h2>Welcome to<span>Koło Łowieckie Boryna w Borkowie Nadrzecznym</span></h2>
  <div class="divider"></div>
  <p>Witamy na stronie internetowej Koła Łowieckiego Boryna w Borkowie Nadrzecznym. Nasze koło działa od 1945 roku, prowadząc gospodarkę łowiecką w okolicznych lasach. Dbamy o zwierzynę, przyrodę i tradycję, łącząc pasję myśliwych z troską o las oraz jego mieszkańców, małych i dużych.</p>
  <p>Zapraszamy do zapoznania się z historią koła, terenami łowieckimi, aktualnościami oraz kalendarzem polowań.</p>
  <p>Wszelkie pytania prosimy kierować przez formularz kontaktowy.</p>
  <span class="btn">Read more</span>
</section>

<section class="widgets">
  <div class="widget">
    <h3>Quick Question</h3><div class="divider"></div>
    <div class="field-label">Name</div><div class="field"></div>
    <div class="field-label">Email</div><div class="field"></div>
    <div class="field-label">Message</div><div class="field tall"></div>
    <span class="btn">Submit</span>
  </div>
  <div class="widget">
    <h3>Testimonial</h3><div class="divider"></div>
    <p class="quote">„Od lat poluję z kołem Boryna i zawsze czuję się tu jak w domu. Dobra organizacja, koleżeńska atmosfera, szacunek dla zwierzyny i lasu. Każde polowanie to wspaniałe przeżycie, a wspólne ogniska po łowach zostają w pamięci na długo. Polecam wszystkim miłośnikom przyrody.”</p>
    <div class="quote-author">— Marek Wolański</div>
  </div>
  <div class="widget">
    <h3>Fazy Księżyca</h3><div class="divider"></div>
    <div class="field-label">Rok</div><div class="field">2017 ▾</div>
    <div class="field-label">Miesiąc</div><div class="field">Lipiec ▾</div>
    <div class="field-label">Dzień</div><div class="field">1 ▾</div>
    <span class="btn">Pokaż fazy księżyca</span>
  </div>
</section>

<section class="content">
  <div class="content-panel">
    <div class="col gallery">
      <h3>Galeria</h3>
      <div class="g-item"><div class="g-thumb" role="img" aria-label="Myśliwi na polowaniu"></div><div><strong>ROK 2015</strong><span>Wspólne polowanie</span></div></div>
      <div class="g-item"><div class="g-thumb" role="img" aria-label="Pokot po polowaniu"></div><div><strong>ROK 2014</strong><span>Polowanie zbiorowe</span></div></div>
      <div class="g-item"><div class="g-thumb" role="img" aria-label="Spotkanie członków koła"></div><div><strong>ROK 2013</strong><span>Zebranie roczne</span></div></div>
      <span class="btn">More</span>
    </div>
    <div class="col monograph" role="img" aria-label="Ambona w lesie w tle listy monografii">
      <h3>Monografia</h3>
      <ul>
        <li>Historia powstania</li><li>Członkowie honorowi</li><li>Kronika koła</li><li>Gospodarka łowiecka</li><li>Tereny łowieckie</li><li>Sztandar</li><li>Odznaczenia</li><li>Zarząd i władze</li><li>Dokumenty</li>
      </ul>
    </div>
    <div class="col news">
      <h3>News</h3>
      <div class="n-item"><div class="n-thumb" role="img" aria-label="Las jesienią"></div><div><b>20/07/2017</b><span>Zebranie członków koła w sobotę.</span></div></div>
      <div class="n-item"><div class="n-thumb" role="img" aria-label="Dzik w lesie"></div><div><b>15/07/2017</b><span>Nowy plan odstrzału dzików na sezon.</span></div></div>
      <div class="n-item"><div class="n-thumb" role="img" aria-label="Sarna na łące"></div><div><b>08/07/2017</b><span>Liczenie zwierzyny w obwodzie leśnym.</span></div></div>
      <div class="n-item"><div class="n-thumb" role="img" aria-label="Paśnik w lesie"></div><div><b>01/07/2017</b><span>Prace przy paśnikach i ambonach.</span></div></div>
      <div class="n-item"><div class="n-thumb" role="img" aria-label="Myśliwi przy ognisku"></div><div><b>24/06/2017</b><span>Relacja z polowania świętojańskiego.</span></div></div>
      <span class="btn">More</span>
    </div>
  </div>
</section>

<section class="hunters" role="img" aria-label="Grupa myśliwych z psami w lesie"></section>

<footer class="site-footer">
  <div class="footer-cols">
    <div>
      <h4>Quick Links</h4><div class="divider"></div>
      <div class="links">
        <ul><li>Home</li><li>About Us</li><li>Hunting Area</li><li>Hunting Offer</li><li>Hunting Season</li></ul>
        <ul><li>Weather</li><li>News</li><li>Gallery</li><li>Contact</li></ul>
      </div>
    </div>
    <div class="contact">
      <h4>Contact Us</h4><div class="divider"></div>
      ul. Leśna 12<br>39-918 Borków Nadrzeczny<br>Polska<br>T: +48 15 000 11 22<br>E: biuro@borynalsw.pl
    </div>
    <div>
      <h4>Keep in Touch</h4><div class="divider"></div>
      <ul class="social"><li><i></i>Społeczność</li><li><i></i>Komunikaty</li><li><i></i>Fotorelacje</li><li><i></i>Filmy z łowiska</li></ul>
    </div>
    <div class="newsletter">
      <h4>Get The Subscribe Newsletter</h4><div class="divider"></div>
      Zapisz się, aby otrzymywać informacje o polowaniach, zebraniach i wydarzeniach koła.
      <div class="subscribe"><div class="field">Enter your email address</div><span class="btn">Subscribe</span></div>
    </div>
  </div>
  <div class="copyright">© 2017 Koło Łowieckie Boryna w Borkowie Nadrzecznym. All Rights Reserved.</div>
</footer>
</body>
</html>
```